Billiards 50th Anniversary Calendar

Need a custom calendar designed to finish at 8.5 x 11. and to be supplied as a pdf print file including .25 bleed on all sides. Total is 24 pages. I will supply one image per calendar month. Cover to have a collage of monthly images or samples of some of your favorites incorporated with a cool design that transitions throughout the calendar. The client's 50th Anniversary logo must be incorporated into the design.

Back cover has a group image to be incorporated as well.

Target Market(s)

Calendar is selling to their billiard clients

Industry/Entity Type

Male dominant industry

Requirements
Must have
• Must have a design element that continues through the calendar but flows with the images well. One image per calendar month.

```html
<!DOCTYPE html>
<html lang="en">
<head>
<meta charset="utf-8">
<title>Cue Corner Billiards — 2022 Calendar Pages</title>
<link href="https://fonts.googleapis.com/css2?family=Roboto:wght@400;500&display=swap" rel="stylesheet">
<style>
:root{
  --paper:#ffffff;
  --ink:#333333;
  --year:#3a3a3a;
  --green:#1d9a48;
  --orange:#ec8a23;
  --sunday:#e4232a;
  --head-grey:#d2d2d2;
  --rule:#cfcfcf;
  --frame:#c8c8c8;
}
*{box-sizing:border-box;margin:0;padding:0}
html,body{width:1200px;height:923px;overflow:hidden;background:var(--paper)}
body{position:relative;font-family:"Roboto",Arial,sans-serif;color:var(--ink)}

.cover-mark{position:absolute;left:55px;top:50px;width:259px;height:199px;border:1px solid var(--frame);
  display:flex;align-items:center;justify-content:center}
.cover-mark .brand-name{font-size:22px;font-weight:500;color:var(--green);text-align:center;line-height:1.2}

.month{position:absolute;width:258px;height:398px;background:var(--paper)}
.photo{position:absolute;left:0;top:0;width:258px;height:199px}
.month-title{position:absolute;left:0;top:203px;width:258px;text-align:center;font-size:17px;font-weight:400;letter-spacing:-.2px}
.month-title .year{color:var(--year)}
.green .month-name{color:var(--green)}
.orange .month-name{color:var(--orange)}
.mini-brand{position:absolute;left:214px;top:206px;width:32px;font-size:5px;font-weight:500;line-height:1.2;color:var(--green);text-align:center}

.days{position:absolute;left:8px;top:230px;width:243px;display:grid;grid-template-columns:repeat(7,1fr);
  border-left:1px solid var(--rule)}
.days .dow{height:6px;background:var(--head-grey);font-size:2.6px;font-weight:500;text-align:center;line-height:6px;color:#555;letter-spacing:.1px}
.days .dow.sun{background:var(--sunday);color:#fff}
.days .cell{position:relative;height:30px;border-right:1px solid var(--rule);border-bottom:1px solid var(--rule);
  font-size:7.5px;text-align:right;padding:2px 3px 0 0}
.days .cell.sun{color:var(--sunday)}
.days .cell .late{position:absolute;left:3px;bottom:1px}
.days .cell svg{position:absolute;left:0;top:0;width:100%;height:100%}

.foot-bar{position:absolute;left:0;top:394px;width:258px;height:4px}
.bar-orange{background:var(--orange)}
.bar-green{background:var(--green)}
</style>
</head>
<body>

<div class="cover-mark"><span class="brand-name">Cue Corner Billiards</span></div>

<!-- January -->
<section class="month green" style="left:332px;top:50px">
  <div class="photo" role="img" aria-label="Pin-up model in black dress lying on a blue pool table with cue and balls" style="background:linear-gradient(180deg,#141414 0%,#1e1a1a 45%,#2e7fb6 80%,#3aa0d8 100%)"></div>
  <h2 class="month-title"><span class="month-name">JANUARY</span><span class="year">2022</span></h2>
  <div class="mini-brand">CUE CORNER</div>
  <div class="days">
    <div class="dow sun">SUNDAY</div><div class="dow">MONDAY</div><div class="dow">TUESDAY</div><div class="dow">WEDNESDAY</div><div class="dow">THURSDAY</div><div class="dow">FRIDAY</div><div class="dow">SATURDAY</div>
    <div class="cell sun"></div><div class="cell"></div><div class="cell"></div><div class="cell"></div><div class="cell"></div><div class="cell"></div><div class="cell">1</div>
    <div class="cell sun">2</div><div class="cell">3</div><div class="cell">4</div><div class="cell">5</div><div class="cell">6</div><div class="cell">7</div><div class="cell">8</div>
    <div class="cell sun">9</div><div class="cell">10</div><div class="cell">11</div><div class="cell">12</div><div class="cell">13</div><div class="cell">14</div><div class="cell">15</div>
    <div class="cell sun">16</div><div class="cell">17</div><div class="cell">18</div><div class="cell">19</div><div class="cell">20</div><div class="cell">21</div><div class="cell">22</div>
    <div class="cell sun"><svg viewBox="0 0 34 30" preserveAspectRatio="none"><line x1="0" y1="0" x2="34" y2="30" stroke="#cfcfcf" stroke-width=".6"/></svg>23<span class="late">30</span></div>
    <div class="cell"><svg viewBox="0 0 34 30" preserveAspectRatio="none"><line x1="0" y1="0" x2="34" y2="30" stroke="#cfcfcf" stroke-width=".6"/></svg>24<span class="late">31</span></div>
    <div class="cell">25</div><div class="cell">26</div><div class="cell">27</div><div class="cell">28</div><div class="cell">29</div>
  </div>
  <div class="foot-bar bar-orange"></div>
</section>

<!-- February -->
<section class="month orange" style="left:609px;top:50px">
  <div class="photo" role="img" aria-label="Pin-up model in leopard jumpsuit seated on a pool table holding a rack" style="background:linear-gradient(180deg,#0f0f0f 0%,#1a1614 50%,#6b5436 75%,#2f86bd 100%)"></div>
  <h2 class="month-title"><span class="month-name">FEBRUARY</span><span class="year">2022</span></h2>
  <div class="mini-brand">CUE CORNER</div>
  <div class="days">
    <div class="dow sun">SUNDAY</div><div class="dow">MONDAY</div><div class="dow">TUESDAY</div><div class="dow">WEDNESDAY</div><div class="dow">THURSDAY</div><div class="dow">FRIDAY</div><div class="dow">SATURDAY</div>
    <div class="cell sun"></div><div class="cell"></div><div class="cell">1</div><div class="cell">2</div><div class="cell">3</div><div class="cell">4</div><div class="cell">5</div>
    <div class="cell sun">6</div><div class="cell">7</div><div class="cell">8</div><div class="cell">9</div><div class="cell">10</div><div class="cell">11</div><div class="cell">12</div>
    <div class="cell sun">13</div><div class="cell">14</div><div class="cell">15</div><div class="cell">16</div><div class="cell">17</div><div class="cell">18</div><div class="cell">19</div>
    <div class="cell sun">20</div><div class="cell">21</div><div class="cell">22</div><div class="cell">23</div><div class="cell">24</div><div class="cell">25</div><div class="cell">26</div>
    <div class="cell sun">27</div><div class="cell">28</div><div class="cell"></div><div class="cell"></div><div class="cell"></div><div class="cell"></div><div class="cell"></div>
  </div>
  <div class="foot-bar bar-green"></div>
</section>

<!-- March -->
<section class="month green" style="left:886px;top:50px">
  <div class="photo" role="img" aria-label="Pin-up model in red polka-dot dress lying on a blue pool table" style="background:linear-gradient(180deg,#141414 0%,#2a2220 45%,#2c8cc6 78%,#3db0e6 100%)"></div>
  <h2 class="month-title"><span class="month-name">MARCH</span><span class="year">2022</span></h2>
  <div class="mini-brand">CUE CORNER</div>
  <div class="days">
    <div class="dow sun">SUNDAY</div><div class="dow">MONDAY</div><div class="dow">TUESDAY</div><div class="dow">WEDNESDAY</div><div class="dow">THURSDAY</div><div class="dow">FRIDAY</div><div class="dow">SATURDAY</div>
    <div class="cell sun"></div><div class="cell"></div><div class="cell">1</div><div class="cell">2</div><div class="cell">3</div><div class="cell">4</div><div class="cell">5</div>
    <div class="cell sun">6</div><div class="cell">7</div><div class="cell">8</div><div class="cell">9</div><div class="cell">10</div><div class="cell">11</div><div class="cell">12</div>
    <div class="cell sun">13</div><div class="cell">14</div><div class="cell">15</div><div class="cell">16</div><div class="cell">17</div><div class="cell">18</div><div class="cell">19</div>
    <div class="cell sun">20</div><div class="cell">21</div><div class="cell">22</div><div class="cell">23</div><div class="cell">24</div><div class="cell">25</div><div class="cell">26</div>
    <div class="cell sun">27</div><div class="cell">28</div><div class="cell">29</div><div class="cell">30</div><div class="cell">31</div><div class="cell"></div><div class="cell"></div>
  </div>
  <div class="foot-bar bar-orange"></div>
</section>

<!-- April -->
<section class="month orange" style="left:332px;top:475px">
  <div class="photo" role="img" aria-label="Pin-up model lining up a shot across a blue pool table" style="background:linear-gradient(160deg,#161412 0%,#3a2a20 35%,#3aa6d6 60%,#4ab8e4 100%)"></div>
  <h2 class="month-title"><span class="month-name">APRIL</span><span class="year">2022</span></h2>
  <div class="mini-brand">CUE CORNER</div>
  <div class="days">
    <div class="dow sun">SUNDAY</div><div class="dow">MONDAY</div><div class="dow">TUESDAY</div><div class="dow">WEDNESDAY</div><div class="dow">THURSDAY</div><div class="dow">FRIDAY</div><div class="dow">SATURDAY</div>
    <div class="cell sun"></div><div class="cell"></div><div class="cell"></div><div class="cell"></div><div class="cell"></div><div class="cell">1</div><div class="cell">2</div>
    <div class="cell sun">3</div><div class="cell">4</div><div class="cell">5</div><div class="cell">6</div><div class="cell">7</div><div class="cell">8</div><div class="cell">9</div>
    <div class="cell sun">10</div><div class="cell">11</div><div class="cell">12</div><div class="cell">13</div><div class="cell">14</div><div class="cell">15</div><div class="cell">16</div>
    <div class="cell sun">17</div><div class="cell">18</div><div class="cell">19</div><div class="cell">20</div><div class="cell">21</div><div class="cell">22</div><div class="cell">23</div>
    <div class="cell sun">24</div><div class="cell">25</div><div class="cell">26</div><div class="cell">27</div><div class="cell">28</div><div class="cell">29</div><div class="cell">30</div>
  </div>
  <div class="foot-bar bar-green"></div>
</section>

<!-- May -->
<section class="month green" style="left:609px;top:475px">
  <div class="photo" role="img" aria-label="Pin-up model in floral dress seated on a pool table beneath a neon bar sign" style="background:linear-gradient(180deg,#1a1c1a 0%,#2a2c2a 45%,#3c4a44 75%,#2f6f5a 100%)"></div>
  <h2 class="month-title"><span class="month-name">MAY</span><span class="year">2022</span></h2>
  <div class="mini-brand">CUE CORNER</div>
  <div class="days">
    <div class="dow sun">SUNDAY</div><div class="dow">MONDAY</div><div class="dow">TUESDAY</div><div class="dow">WEDNESDAY</div><div class="dow">THURSDAY</div><div class="dow">FRIDAY</div><div class="dow">SATURDAY</div>
    <div class="cell sun">1</div><div class="cell">2</div><div class="cell">3</div><div class="cell">4</div><div class="cell">5</div><div class="cell">6</div><div class="cell">7</div>
    <div class="cell sun">8</div><div class="cell">9</div><div class="cell">10</div><div class="cell">11</div><div class="cell">12</div><div class="cell">13</div><div class="cell">14</div>
    <div class="cell sun">15</div><div class="cell">16</div><div class="cell">17</div><div class="cell">18</div><div class="cell">19</div><div class="cell">20</div><div class="cell">21</div>
    <div class="cell sun">22</div><div class="cell">23</div><div class="cell">24</div><div class="cell">25</div><div class="cell">26</div><div class="cell">27</div><div class="cell">28</div>
    <div class="cell sun">29</div><div class="cell">30</div><div class="cell">31</div><div class="cell"></div><div class="cell"></div><div class="cell"></div><div class="cell"></div>
  </div>
  <div class="foot-bar bar-orange"></div>
</section>

<!-- June -->
<section class="month orange" style="left:886px;top:475px">
  <div class="photo" role="img" aria-label="Smiling pin-up model lying on a blue pool table holding cues" style="background:linear-gradient(180deg,#111111 0%,#241e1a 45%,#2a86c2 78%,#3aa8e0 100%)"></div>
  <h2 class="month-title"><span class="month-name">JUNE</span><span class="year">2022</span></h2>
  <div class="mini-brand">CUE CORNER</div>
  <div class="days">
    <div class="dow sun">SUNDAY</div><div class="dow">MONDAY</div><div class="dow">TUESDAY</div><div class="dow">WEDNESDAY</div><div class="dow">THURSDAY</div><div class="dow">FRIDAY</div><div class="dow">SATURDAY</div>
    <div class="cell sun"></div><div class="cell"></div><div class="cell"></div><div class="cell">1</div><div class="cell">2</div><div class="cell">3</div><div class="cell">4</div>
    <div class="cell sun">5</div><div class="cell">6</div><div class="cell">7</div><div class="cell">8</div><div class="cell">9</div><div class="cell">10</div><div class="cell">11</div>
    <div class="cell sun">12</div><div class="cell">13</div><div class="cell">14</div><div class="cell">15</div><div class="cell">16</div><div class="cell">17</div><div class="cell">18</div>
    <div class="cell sun">19</div><div class="cell">20</div><div class="cell">21</div><div class="cell">22</div><div class="cell">23</div><div class="cell">24</div><div class="cell">25</div>
    <div class="cell sun">26</div><div class="cell">27</div><div class="cell">28</div><div class="cell">29</div><div class="cell">30</div><div class="cell"></div><div class="cell"></div>
  </div>
  <div class="foot-bar bar-green"></div>
</section>

</body>
</html>
```